food delivery web site design

Currently we have a smartphone app (ios/android) that is being used by our clients to make orders to about 30 different restaurants.

We would like to extent this and have also a website that is able to mimic the same functionalities:
- register
- show restaurants based on the selected address
- make order to an restaurant
- being able to process orders for other registered users (please read the attached doc for complete info on this)

Take a look at the attached doc for more info.

```html
<!DOCTYPE html>
<html lang="ro">
<head>
<meta charset="utf-8">
<title>Mealio – Restaurante</title>
<link href="https://fonts.googleapis.com/css2?family=Oswald:wght@300;400&family=Open+Sans:wght@400&display=swap" rel="stylesheet">
<style>
:root{
  --red:#9c1a0c;
  --red-dark:#7e1408;
  --gold:#d4a514;
  --ink:#2b2b2b;
  --grey:#9a9a9a;
  --rule:#d6d6d6;
  --footer:#1c1c1c;
  --pattern:#f1f1f1;
  --green:#4aa52a;
}
*{margin:0;padding:0;box-sizing:border-box}
html,body{width:1200px;height:923px;overflow:hidden;background:#fff}
body{position:relative;font-family:'Open Sans',sans-serif;color:var(--ink)}

.site-header{position:absolute;left:0;top:0;width:1200px;height:104px}
.header-pattern{position:absolute;left:0;top:0;width:1200px;height:50px;background:linear-gradient(180deg,#f7f7f7,var(--pattern))}
.header-bar{position:absolute;left:0;top:50px;width:1200px;height:54px;background:var(--red);border-top:2px solid var(--red-dark);border-bottom:2px solid var(--red-dark)}
.bar-line{position:absolute;top:26px;height:0;border-top:1px solid rgba(255,255,255,.75)}
.bar-line.dotted{border-top-style:dotted}
.call-us{position:absolute;left:350px;top:10px;font-family:'Oswald',sans-serif;font-size:25px;line-height:32px;color:#fff;letter-spacing:-.3px}
.call-us .phone{color:#f3c623}
.call-us svg{vertical-align:-3px;margin:0 2px 0 4px}
.account-links{position:absolute;left:905px;top:16px;display:flex;gap:22px;font-family:'Oswald',sans-serif;font-size:15px;color:#fff;line-height:20px}
.account-links a{color:#fff;text-decoration:none;display:flex;align-items:center;gap:6px}

.brand-badge{position:absolute;left:138px;top:0;width:157px;height:160px}
.brand-name{position:absolute;left:0;top:52px;width:157px;text-align:center;font-family:'Oswald',sans-serif;font-size:26px;color:var(--red)}

.results{position:absolute;left:138px;top:222px;width:923px}
.results-title{height:56px;border-bottom:1px solid var(--rule);display:flex;align-items:baseline;gap:6px}
.results-title .label{font-family:'Oswald',sans-serif;font-size:18px;color:var(--grey);letter-spacing:-.3px}
.results-title .address{font-size:22px;color:var(--ink)}

.restaurant{position:relative;height:167px;border-bottom:1px dotted #bdbdbd}
.restaurant:first-of-type{height:178px}
.restaurant:last-of-type{border-bottom:1px solid var(--rule)}
.restaurant-photo{position:absolute;left:2px;top:36px;width:130px;height:103px}
.restaurant:first-of-type .restaurant-photo{top:39px}
.corner{position:absolute;left:2px;top:36px;width:0;height:0;border-top:20px solid var(--green);border-right:20px solid transparent}
.restaurant:first-of-type .corner{top:39px}
.corner.closed{border-top-color:#8a8a8a}
.restaurant-info{position:absolute;left:158px;top:30px}
.restaurant:first-of-type .restaurant-info{top:33px}
.restaurant-name{font-family:'Oswald',sans-serif;font-weight:400;font-size:38px;line-height:46px;color:#2d2d2d}
.stars{font-size:16px;color:var(--gold);letter-spacing:4px;line-height:20px;margin-top:2px}
.meta{display:flex;margin-top:12px;font-family:'Oswald',sans-serif;font-weight:300;font-size:19px;line-height:24px;color:#222}
.meta li{list-style:none;display:flex;align-items:center;gap:8px}
.meta .distance{width:108px}
.meta .price{width:132px}
.order-btn{position:absolute;right:28px;top:93px;height:46px;padding:0 10px;background:var(--red);color:#fff;font-family:'Oswald',sans-serif;font-size:19px;line-height:46px;text-decoration:none}
.restaurant:first-of-type .order-btn{top:96px}

.site-footer{position:absolute;left:0;top:868px;width:1200px;height:55px;background:var(--footer);border-top:3px solid #333}
.footer-nav{position:absolute;left:138px;top:16px;display:flex;font-size:12.5px;color:#eee}
.footer-nav a{color:#eee;text-decoration:none}
.footer-nav span{color:#555;margin:0 9px}
.copyright{position:absolute;right:138px;top:16px;font-size:12.5px;color:#eee}
</style>
</head>
<body>

<header class="site-header">
  <div class="header-pattern" role="img" aria-label="Fundal decorativ cu ilustrații de mâncare"></div>
  <div class="header-bar">
    <span class="bar-line" style="left:296px;width:37px"></span>
    <span class="bar-line dotted" style="left:610px;width:276px"></span>
    <span class="bar-line" style="left:1064px;width:136px"></span>
    <div class="call-us">SUNĂ-NE LA<svg width="14" height="20" viewBox="0 0 14 20"><path d="M3 1l3 0 1 5-2 1c0 3 2 6 4 7l2-1 2 4-3 2C5 18 1 12 1 5z" fill="#f3c623"/></svg><span class="phone">0700 123 456</span></div>
    <nav class="account-links">
      <a href="#"><svg width="14" height="12" viewBox="0 0 14 12"><path d="M8 0l6 5-6 5V7C4 7 2 8 1 11 1 6 3 3 8 3z" fill="#fff"/></svg>LOGIN</a>
      <a href="#"><svg width="16" height="12" viewBox="0 0 16 12"><circle cx="6" cy="3.5" r="3" fill="#fff"/><path d="M0 12c0-4 3-5 6-5s6 1 6 5z" fill="#fff"/><path d="M13 1v5M10.5 3.5h5" stroke="#fff" stroke-width="1.5"/></svg>SIGN IN</a>
    </nav>
  </div>
  <div class="brand-badge">
    <svg width="157" height="160" viewBox="0 0 157 160">
      <polygon points="0,0 157,0 157,132 135,157 22,157 0,132" fill="var(--red)"/>
      <polygon points="6,0 151,0 151,129 132,151 25,151 6,129" fill="none" stroke="rgba(255,255,255,.35)" stroke-width="1"/>
      <circle cx="78.5" cy="77" r="55" fill="#fff"/>
    </svg>
    <div class="brand-name">Mealio</div>
  </div>
</header>

<main class="results">
  <h1 class="results-title"><span class="label">3 REZULTATE PENTRU ADRESA:</span><span class="address">Lorem ipsum dolor sit amet, consectetur adipiscing elit.</span></h1>

  <article class="restaurant">
    <div class="restaurant-photo" role="img" aria-label="Imagine restaurant Hanul Bunicii" style="background:linear-gradient(135deg,#8a6a46,#5d4430)"></div>
    <span class="corner"></span>
    <div class="restaurant-info">
      <h2 class="restaurant-name">Hanul Bunicii</h2>
      <div class="stars">★★★★★</div>
      <ul class="meta">
        <li class="distance"><svg width="18" height="20" viewBox="0 0 18 20"><rect x="8" y="0" width="2.5" height="20" fill="var(--red)"/><path d="M1 3h15l2 2-2 2H1z" fill="var(--red)"/><path d="M17 10H2l-2 2 2 2h15z" fill="var(--red)"/></svg>3KM</li>
        <li class="price"><svg width="20" height="14" viewBox="0 0 20 14"><rect x="0" y="0" width="12" height="3.5" rx="1.7" fill="var(--red)"/><rect x="0" y="5" width="12" height="3.5" rx="1.7" fill="var(--red)"/><rect x="0" y="10" width="12" height="3.5" rx="1.7" fill="var(--red)"/><rect x="13" y="5" width="7" height="3.5" rx="1.7" fill="var(--red)"/><rect x="13" y="10" width="7" height="3.5" rx="1.7" fill="var(--red)"/></svg>&lt; 25RON</li>
        <li class="cuisine"><svg width="20" height="20" viewBox="0 0 20 20"><path d="M2 4l14 14" stroke="var(--red)" stroke-width="3"/><path d="M6 1l3 3-4 4-3-3z" fill="var(--red)"/></svg>ROMANESC</li>
      </ul>
    </div>
    <a class="order-btn" href="#">COMANDĂ DE AICI</a>
  </article>

  <article class="restaurant">
    <div class="restaurant-photo" role="img" aria-label="Imagine restaurant Trattoria Oliva" style="background:linear-gradient(180deg,#ffffff,#eef0ec 60%,#e9ece6)"></div>
    <span class="corner"></span>
    <div class="restaurant-info">
      <h2 class="restaurant-name">Trattoria Oliva</h2>
      <div class="stars">★★★★★</div>
      <ul class="meta">
        <li class="distance"><svg width="18" height="20" viewBox="0 0 18 20"><rect x="8" y="0" width="2.5" height="20" fill="var(--red)"/><path d="M1 3h15l2 2-2 2H1z" fill="var(--red)"/><path d="M17 10H2l-2 2 2 2h15z" fill="var(--red)"/></svg>12KM</li>
        <li class="price"><svg width="20" height="14" viewBox="0 0 20 14"><rect x="0" y="0" width="12" height="3.5" rx="1.7" fill="var(--red)"/><rect x="0" y="5" width="12" height="3.5" rx="1.7" fill="var(--red)"/><rect x="0" y="10" width="12" height="3.5" rx="1.7" fill="var(--red)"/><rect x="13" y="5" width="7" height="3.5" rx="1.7" fill="var(--red)"/><rect x="13" y="10" width="7" height="3.5" rx="1.7" fill="var(--red)"/></svg>&lt; 50RON</li>
        <li class="cuisine"><svg width="20" height="20" viewBox="0 0 20 20"><path d="M2 4l14 14" stroke="var(--red)" stroke-width="3"/><path d="M6 1l3 3-4 4-3-3z" fill="var(--red)"/></svg>ITALIAN</li>
      </ul>
    </div>
    <a class="order-btn" href="#">ALEGE RESTAURANT</a>
  </article>

  <article class="restaurant">
    <div class="restaurant-photo" role="img" aria-label="Imagine restaurant the STUDIO" style="background:linear-gradient(180deg,#ffffff,#f2f2f2)"></div>
    <span class="corner closed"></span>
    <div class="restaurant-info">
      <h2 class="restaurant-name">the STUDIO</h2>
      <div class="stars">★★★★☆</div>
      <ul class="meta">
        <li class="distance"><svg width="18" height="20" viewBox="0 0 18 20"><rect x="8" y="0" width="2.5" height="20" fill="var(--red)"/><path d="M1 3h15l2 2-2 2H1z" fill="var(--red)"/><path d="M17 10H2l-2 2 2 2h15z" fill="var(--red)"/></svg>14KM</li>
        <li class="price"><svg width="20" height="14" viewBox="0 0 20 14"><rect x="0" y="0" width="12" height="3.5" rx="1.7" fill="var(--red)"/><rect x="0" y="5" width="12" height="3.5" rx="1.7" fill="var(--red)"/><rect x="0" y="10" width="12" height="3.5" rx="1.7" fill="var(--red)"/><rect x="13" y="5" width="7" height="3.5" rx="1.7" fill="var(--red)"/><rect x="13" y="10" width="7" height="3.5" rx="1.7" fill="var(--red)"/></svg>&lt; 75RON</li>
        <li class="cuisine"><svg width="20" height="20" viewBox="0 0 20 20"><path d="M2 4l14 14" stroke="var(--red)" stroke-width="3"/><path d="M6 1l3 3-4 4-3-3z" fill="var(--red)"/></svg>CONTEMPORAN, INTERNATIONAL</li>
      </ul>
    </div>
    <a class="order-btn" href="#">VEZI MENIUL</a>
  </article>
</main>

<footer class="site-footer">
  <nav class="footer-nav">
    <a href="#">Contactează-ne</a><span>|</span>
    <a href="#">Despre noi</a><span>|</span>
    <a href="#">Parteneri noștri</a><span>|</span>
    <a href="#">FAQ</a><span>|</span>
    <a href="#">Devino partener</a>
  </nav>
  <p class="copyright">Copyright © 2013 Mealio.ro. Toate drepturile rezervate.</p>
</footer>

</body>
</html>
```